Torvane Halbridge

Looking for modern business cards.
Clean contemporary design.
Similar to this.
https://www.plumvexa-search.example/imgres?imgurl=https%3A%2F%2Fimg.quorlint-cdn.example%2Fsleek_dark_metal_card_design_540.jpg&imgrefurl=https%3A%2F%2Fwww.quorlint-prints.example%2Fsleek_dark_metal_card_design-918273645501928374&q=modern%20business%20cards

But I'd like the blue to look metallic.

Business

```html
<!DOCTYPE html>
<html lang="en">
<head>
<meta charset="utf-8">
<title>Torvane Halbridge – Business Cards</title>
<link rel="stylesheet" href="https://fonts.googleapis.com/css2?family=Lato:wght@400;700&display=swap">
<style>
  :root {
    --page-bg: #eceef0;
    --card-dark: #1c1d1f;
    --card-light: #ffffff;
    --steel-deep: #1f5670;
    --steel-deep-hi: #3d7f9c;
    --steel-bright: #1ba3c6;
    --steel-bright-hi: #7fd3ea;
    --ink: #1f2a33;
    --accent-dot: #e8401c;
  }
  * { box-sizing: border-box; margin: 0; padding: 0; }
  html, body { width: 1200px; height: 900px; overflow: hidden; }
  body {
    background: var(--page-bg);
    font-family: "Lato", sans-serif;
    display: flex;
    align-items: center;
    justify-content: center;
    gap: 60px;
  }
  .card {
    position: relative;
    width: 525px;
    height: 300px;
    border-radius: 3px;
    box-shadow: 0 10px 30px rgba(0,0,0,0.18);
    overflow: hidden;
  }
  .card--front { background: var(--card-dark); }
  .card--back { background: var(--card-light); }

  .brand {
    position: absolute;
    display: flex;
    align-items: center;
    gap: 10px;
    font-weight: 700;
    font-size: 28px;
    letter-spacing: 0.2px;
  }
  .brand__dot {
    width: 10px; height: 10px; border-radius: 50%;
    background: var(--accent-dot);
  }
  .card--front .brand { left: 140px; top: 128px; color: var(--steel-bright); }
  .card--back .brand { right: 34px; top: 54px; font-size: 24px; color: var(--steel-bright); }

  .person { position: absolute; left: 44px; top: 158px; }
  .person__name { font-weight: 700; font-size: 21px; letter-spacing: 0.4px; color: var(--steel-deep); }
  .person__name span { color: var(--steel-bright); }
  .person__role { font-size: 15px; color: var(--ink); margin-top: 1px; }

  .contact { position: absolute; left: 44px; top: 214px; list-style: none; }
  .contact li { display: flex; align-items: center; gap: 8px; font-size: 14px; color: var(--ink); line-height: 19px; }
  .contact svg { width: 12px; height: 12px; fill: var(--steel-deep); }

  .band { position: absolute; left: 0; bottom: 0; width: 100%; height: 24px; }
</style>
</head>
<body>
  <section class="card card--front" aria-label="Card front">
    <div class="brand"><span class="brand__dot"></span>Torvane Halbridge</div>
  </section>

  <section class="card card--back" aria-label="Card back">
    <div class="brand"><span class="brand__dot"></span>Torvane Halbridge</div>

    <div class="person">
      <p class="person__name">EDRIC <span>VALLOW</span></p>
      <p class="person__role">Managing Director</p>
    </div>

    <ul class="contact">
      <li><svg viewBox="0 0 12 12"><path d="M2 1h2.5l1 3-1.5 1a7 7 0 0 0 3 3l1-1.5 3 1V10a1 1 0 0 1-1 1A9 9 0 0 1 1 2a1 1 0 0 1 1-1z"/></svg>201 555 0147</li>
      <li><svg viewBox="0 0 12 12"><path d="M0 2h12v8H0z M1 3v.4l5 3.3 5-3.3V3z" fill-rule="evenodd"/></svg>info@torvanehalbridge.example</li>
      <li><svg viewBox="0 0 12 12"><circle cx="6" cy="6" r="5.5"/></svg>www.torvanehalbridge.example</li>
    </ul>

    <svg class="band" viewBox="0 0 525 24" preserveAspectRatio="none" aria-hidden="true">
      <defs>
        <linearGradient id="steelDeep" x1="0" y1="0" x2="0" y2="1">
          <stop offset="0" stop-color="var(--steel-deep-hi)"/>
          <stop offset="0.45" stop-color="var(--steel-deep)"/>
          <stop offset="1" stop-color="#143a4d"/>
        </linearGradient>
        <linearGradient id="steelBright" x1="0" y1="0" x2="0" y2="1">
          <stop offset="0" stop-color="var(--steel-bright-hi)"/>
          <stop offset="0.5" stop-color="var(--steel-bright)"/>
          <stop offset="1" stop-color="#137f9c"/>
        </linearGradient>
      </defs>
      <rect x="0" y="6" width="310" height="18" fill="url(#steelDeep)"/>
      <rect x="310" y="0" width="215" height="16" fill="url(#steelBright)"/>
      <rect x="310" y="16" width="215" height="8" fill="url(#steelDeep)"/>
    </svg>
  </section>
</body>
</html>
```